Paws of Kindness Comfort & Dog Training

I have a dual themed business. I am a nationally recognized dog trainer for NCR (National Canine Registry) and Tail Allies (Pet Therapy). One side of my business card will need to address my pet therapy ministry called "Paws of Kindness Comfort". We visit almost 1,000 people a month bringing emotionally uplifting happy visits for nursing homes, veterans hospitals, hospice care, surgery recovery, school systems, and libraries, etc. In addition to emotionally positive effects, pet therapy also helps with anxiety, mobility, regulating blood pressure, and many more advantages. I've attached 2 graphics that are connected with this ministry; #1 paw print inside ribbon heart, #2 clasping hands sketch. The story behind the clasping hands is that it is an actual picture of my hand holding my mother's hand on her death bed (with a sketch filter used). My mother lived in a different state than I live in, and I had wished she had pet therapy available to her in her last months of life. They would have provided some bright moments to her difficult days. So, I vowed that although I was not able to help my own mother, I could train my own dog to reach out to hundreds of people in the community I live in. I have continued to live up to that vow, and have gone on to become a national trainer for other people who would like to train their pets to do the same thing.SIDE TWO of my business card will be announcing that I am a dog trainer for puppies, basic obedience, pet therapy, ESA (emotional support animals), and service dogs. Additionally, I offer canine body language training, dog agility training, and cognitive training. I have also attached two graphics for this side: #1 NCR logo, #2 Tail Allies Evaluation

Target Market(s)

Industry/Entity Type

Dog Training

Contact Information for Business Card

I'm looking for a designer who is good with color scheme & fonts.
2-sided card
one side for pet therapy
one side for dog training

Logo Text

Paws of KindnessComfort

Font styles to use
Sans Serif
Decorative

Colors

Designer to choose colors to be used in the design.

Requirements
Must have
• -Contact information: Marla Quinby (555) 926-3140
• - Contact information for online: Paws of Kindness Comfort (Facebook, Instagram & Twitter)
• - Graphics for pet therapy: clasping hands
• - Graphics for dog training: NCR Canine Fine Neighbor, Tail Allies
• - List of dog training classes I offer: Basic Obedience, NCR Canine Fine Neighbor, NCR B.R.I.G.H.T. Puppy, Pet Therapy training, ESA (Emotional Support Animal), Service Dog training, Canine Body Language, Dog Agility, Cognitive Training, Dog Trick Training
Nice to have
• appealing graphic for dog training school
• Titles in decorative font (but still easy to read) & detail info in very easy to read font

```html
<!DOCTYPE html>
<html lang="en">
<head>
<meta charset="utf-8">
<title>Paws of Kindness Comfort &amp; Dog Training – Business Card</title>
<link href="https://fonts.googleapis.com/css2?family=Alfa+Slab+One&family=Source+Sans+3:wght@400;600&family=Roboto+Condensed:wght@300;400;700&family=Great+Vibes&family=Montserrat:wght@600&display=swap" rel="stylesheet">
<style>
  :root {
    --brown: #54401f;
    --brown-dark: #45341a;
    --ink: #4a3a1a;
    --magenta: #c91f56;
    --gold: #e8c830;
    --navy: #2a4a8a;
    --white: #ffffff;
    --paper: #ffffff;
    --tan: #a8915f;
  }
  * { box-sizing: border-box; margin: 0; padding: 0; }
  html, body { width: 1200px; height: 1200px; overflow: hidden; background: var(--paper); }
  body { position: relative; font-family: "Source Sans 3", sans-serif; }

  .card { position: absolute; left: 176px; width: 845px; height: 481px; overflow: hidden; background: var(--white); border: 1px solid var(--brown-dark); }

  /* ---------- Training side ---------- */
  .training { top: 94px; }
  .training__title { position: absolute; top: 38px; left: 0; right: 0; text-align: center; font-family: "Alfa Slab One", serif; font-size: 62px; color: var(--ink); letter-spacing: -0.5px; line-height: 1; }
  .class-list { position: absolute; top: 126px; list-style: none; font-size: 21px; color: var(--ink); line-height: 24px; }
  .class-list--left { left: 126px; }
  .class-list--right { left: 485px; }
  .class-list li { position: relative; padding-left: 26px; white-space: nowrap; }
  .class-list li::before { content: ""; position: absolute; left: 2px; top: 7px; width: 12px; height: 12px; border-radius: 50%; background: var(--magenta); }

  .credentials { position: absolute; top: 282px; left: 0; right: 0; display: flex; justify-content: center; align-items: flex-end; gap: 12px; }
  .badge { width: 60px; height: 72px; display: flex; flex-direction: column; align-items: center; }
  .badge__seal { width: 58px; height: 58px; border-radius: 50%; background: var(--gold); border: 5px solid var(--navy); }
  .badge__tab { width: 58px; height: 12px; margin-top: -4px; background: var(--gold); border: 1px solid var(--ink); }
  .partner { display: flex; flex-direction: column; align-items: center; padding: 0 4px 8px; }
  .partner__mark { width: 38px; height: 38px; border-radius: 50%; border: 3px solid var(--magenta); margin-bottom: 4px; }
  .partner__name { font-weight: 600; font-size: 19px; color: var(--ink); line-height: 1; }

  .training__band { position: absolute; left: 0; right: 0; bottom: 0; height: 103px; background: var(--brown); }
  .name-bar { position: absolute; left: 238px; top: 368px; width: 375px; height: 42px; }
  .name-bar svg { position: absolute; inset: 0; }
  .name-bar__text { position: absolute; inset: 0; text-align: center; font-family: "Roboto Condensed", sans-serif; font-size: 40px; line-height: 42px; color: var(--white); letter-spacing: -1px; }
  .name-bar__text b { font-weight: 700; }
  .name-bar__text span { font-weight: 300; }
  .training__phone { position: absolute; left: 0; right: 0; top: 420px; text-align: center; font-family: "Roboto Condensed", sans-serif; font-size: 31px; color: var(--white); }

  /* ---------- Therapy side ---------- */
  .therapy { top: 624px; height: 482px; width: 842px; }
  .therapy__accents { position: absolute; inset: 0; }
  .therapy__panel { position: absolute; left: 20px; top: 20px; right: 0; bottom: 20px; background: var(--brown); border-radius: 16px 0 0 16px; overflow: hidden; }
  .therapy__hands { position: absolute; left: 460px; top: 0; right: 0; bottom: 0; background: radial-gradient(ellipse at 55% 45%, rgba(190,170,125,0.55), rgba(84,64,31,0) 70%); }
  .therapy__title { position: absolute; left: 0; right: 0; top: 44px; text-align: center; font-family: "Great Vibes", cursive; font-size: 82px; color: var(--white); white-space: nowrap; line-height: 1.2; }
  .tagline { position: absolute; left: 281px; top: 144px; width: 257px; height: 32px; border-radius: 7px; background: var(--magenta); text-align: center; font-family: "Roboto Condensed", sans-serif; font-size: 22px; line-height: 32px; color: var(--white); }
  .portrait { position: absolute; left: 18px; top: 198px; width: 128px; height: 128px; border-radius: 22px; background: linear-gradient(135deg, #7d8a55, #b0825a 55%, #d8d0c0); }
  .person { position: absolute; left: 168px; top: 232px; font-family: "Roboto Condensed", sans-serif; line-height: 1; }
  .person__first { font-weight: 300; font-size: 40px; color: var(--white); }
  .person__last { font-weight: 700; font-size: 40px; color: var(--magenta); margin-top: 6px; }
  .person__role { font-family: "Montserrat", sans-serif; font-size: 12px; letter-spacing: 7px; color: var(--white); margin-top: 10px; }
  .heart-paw { position: absolute; left: 190px; top: 344px; width: 70px; height: 88px; border-radius: 40% 40% 50% 50%; background: radial-gradient(circle at 50% 45%, rgba(170,170,130,0.8), rgba(185,95,50,0.7) 70%); }
  .contacts { position: absolute; left: 332px; top: 246px; list-style: none; font-family: "Montserrat", sans-serif; font-size: 19px; color: var(--white); }
  .contacts li { display: flex; align-items: center; height: 36px; margin-bottom: 1px; white-space: nowrap; }
  .contacts .icon { width: 28px; height: 28px; margin-right: 9px; flex: none; }
  .contacts .dot { width: 22px; height: 22px; margin: 0 12px 0 3px; border-radius: 50%; background: var(--white); flex: none; }
</style>
</head>
<body>

<section class="card training">
  <h1 class="training__title">Dog Training Classes</h1>
  <ul class="class-list class-list--left">
    <li>Basic Obedience</li>
    <li>NCR Canine Fine Neighbor</li>
    <li>NCR B.R.I.G.H.T. Puppy</li>
    <li>Pet Therapy training</li>
    <li>ESA (Emotional Support Animal)</li>
  </ul>
  <ul class="class-list class-list--right">
    <li>Service Dog training</li>
    <li>Dog Agility</li>
    <li>Cognitive Training</li>
    <li>Dog Trick Training</li>
    <li>Canine Body Language</li>
  </ul>

  <div class="credentials">
    <div class="badge" role="img" aria-label="Evaluator credential badge"><div class="badge__seal"></div><div class="badge__tab"></div></div>
    <div class="badge" role="img" aria-label="Instructor credential badge"><div class="badge__seal"></div><div class="badge__tab"></div></div>
    <div class="partner"><div class="partner__mark"></div><div class="partner__name">Tail Allies</div></div>
    <div class="badge" role="img" aria-label="Evaluator credential badge"><div class="badge__seal"></div><div class="badge__tab"></div></div>
    <div class="badge" role="img" aria-label="Evaluator credential badge"><div class="badge__seal"></div><div class="badge__tab"></div></div>
  </div>

  <div class="training__band"></div>
  <div class="name-bar">
    <svg viewBox="0 0 375 42" preserveAspectRatio="none"><polygon points="0,0 375,0 360,42 15,42" fill="var(--magenta)"/></svg>
    <div class="name-bar__text"><span>MARLA</span> <b>QUINBY</b></div>
  </div>
  <div class="training__phone">(555) 926-3140</div>
</section>

<section class="card therapy">
  <svg class="therapy__accents" viewBox="0 0 842 482" preserveAspectRatio="none">
    <polygon points="0,0 262,0 280,24 20,24 20,312 0,275" fill="var(--magenta)"/>
    <polygon points="510,458 842,458 842,482 530,482" fill="var(--magenta)"/>
  </svg>
  <div class="therapy__panel">
    <div class="therapy__hands" role="img" aria-label="Sketch of two clasped hands"></div>
    <h2 class="therapy__title">Paws of Kindness Comfort</h2>
    <div class="tagline">We “PAWS” for Healing</div>
    <div class="portrait" role="img" aria-label="Photo of the director with her small white therapy dog"></div>
    <div class="person">
      <div class="person__first">MARLA</div>
      <div class="person__last">QUINBY</div>
      <div class="person__role">DIRECTOR</div>
    </div>
    <div class="heart-paw" role="img" aria-label="Paw print inside a ribbon heart"></div>
    <ul class="contacts">
      <li>
        <svg class="icon" viewBox="0 0 28 28"><rect width="28" height="28" rx="6" fill="var(--white)"/><path d="M9 6c1 0 2 3 2 4s-2 1-1 3 3 4 4 4 1-1 2-1 4 1 4 2-1 3-3 3C11 21 7 15 7 9c0-2 1-3 2-3z" fill="var(--brown)"/></svg>
        (555) 926 - 3140
      </li>
      <li>
        <svg class="icon" viewBox="0 0 28 28"><rect width="28" height="28" rx="6" fill="var(--white)"/><rect x="6" y="8" width="16" height="12" fill="none" stroke="var(--brown)" stroke-width="1.6"/><polyline points="6,8 14,15 22,8" fill="none" stroke="var(--brown)" stroke-width="1.6"/></svg>
        PawsofKindnessComfort@example.com
      </li>
      <li><span class="dot"></span>Paws of Kindness Comfort</li>
      <li><span class="dot"></span>biscuitquinby</li>
      <li><span class="dot"></span>@Pawsofkindness</li>
    </ul>
  </div>
</section>

</body>
</html>
```